Basic / Quick Business Card

Quick easy design project!

Need a one sided basic business card that matches font & style of brand and bottle label for our gourmet condiment, Brindle Harrow Sauce. Brindle Harrow Sauce is sold in specialty retail, gourmet groceries and appears on chef-driven restaurant menus, so the target market is a high end, gourmet, artisan-made food-loving customer.

Files Included:
Sauce Bottle Label
Brindle Harrow Sauce Round Logos

**About the logos - the logo may be used in a circle or alone vertically as on side of the bottle label**

Layout of Card:
May be vertical or horizontal based on designer ideas.

Logo usage (in circle vs. stand alone vertical logo) is up to designers descretion as well.

Reverse side of business card will be various high end / professional product photos / food shots using us.kelbo.com system. **Designer on this project will NOT design a reserve for the card.**

Paper that will be used for printing:
Kelbo Standard - it's a WHITE paper, but we use a cream background on Brindle Harrow Sauce branding, so please take this into account on design to stay brand consistent.

Elements & Copy for Card:
1. Logo in either script horizontal or vertical version
2. Copy: "Artisan Made - Small Batch"
3. Name - Wes Dorrance
4. Title - Creator
5. Phone - xxx.xxx.xxxx
6. xxxx@brindleharrow.com
7. URL: brindleharrowsauce.com
8. Social Media: @getbrindleharrow on Quillo / Pagora / Lumigrid

Please provide final files in Illustrator or InDesign format.

```html
<!DOCTYPE html>
<html lang="en">
<head>
<meta charset="utf-8">
<title>Brindle Harrow Sauce – Business Card</title>
<link rel="stylesheet" href="https://fonts.googleapis.com/css2?family=Courier+Prime:wght@400;700&display=swap">
<style>
  :root {
    --backdrop: #e6e2dd;
    --card-edge: #111111;
    --cream: #f1efdc;
    --rim: #f7f6ee;
    --amber: #e39b12;
    --ink: #111111;
  }
  * { margin: 0; padding: 0; box-sizing: border-box; }
  html, body {
    width: 1200px; height: 867px; overflow: hidden;
    background: var(--backdrop);
    font-family: "Courier Prime", "Courier New", monospace;
  }
  .card {
    position: absolute; left: 100px; top: 148px;
    width: 1000px; height: 571px;
    background: var(--card-edge);
  }
  .card__face {
    position: absolute; inset: 18px;
    background: var(--rim);
  }
  .card__frame {
    position: absolute; inset: 5px;
    border: 6px solid var(--amber);
    background: var(--cream);
  }
  .card__dashes {
    position: absolute; inset: 18px 16px 16px 16px;
    border: 3px dashed var(--ink);
  }
  .tagline {
    position: absolute; left: 52px; top: 15px;
    padding: 0 10px;
    background: var(--cream);
    color: var(--amber);
    font-size: 21px; font-weight: 400;
    letter-spacing: 0.2px;
  }
  .brand {
    position: absolute; left: 0; right: 0; top: 74px;
    text-align: center; color: var(--ink);
    font-weight: 700; line-height: 1;
  }
  .brand__name { font-size: 62px; letter-spacing: -1px; }
  .brand__name + .brand__name { margin-top: 4px; }
  .brand__kind { font-size: 26px; letter-spacing: 8px; margin-top: 10px; padding-left: 160px; }
  .person {
    position: absolute; left: 0; right: 0; top: 318px;
    text-align: center; color: var(--ink); font-weight: 700;
  }
  .person__name {
    font-size: 30px;
    color: var(--cream);
    -webkit-text-stroke: 1.2px var(--ink);
    text-shadow: 2px 2px 0 var(--ink);
  }
  .person__title { font-size: 24px; letter-spacing: 1px; margin-top: 6px; }
  .contact {
    position: absolute; left: 0; right: 0; top: 404px;
    text-align: center; color: var(--ink);
    font-size: 17px; font-weight: 700;
  }
  .social {
    position: absolute; left: 0; right: 0; top: 446px;
    display: flex; justify-content: center; gap: 26px;
    color: var(--amber); font-size: 19px; font-weight: 700;
  }
  .social__item { display: flex; align-items: center; gap: 8px; }
  .social__mark { width: 20px; height: 20px; background: var(--amber); border-radius: 3px; }
</style>
</head>
<body>
  <div class="card">
    <div class="card__face">
      <div class="card__frame">
        <div class="card__dashes"></div>
        <div class="tagline">Artisan Made - Small Batch</div>
        <div class="brand">
          <div class="brand__name">Brindle</div>
          <div class="brand__name">Harrow</div>
          <div class="brand__kind">sauce</div>
        </div>
        <div class="person">
          <div class="person__name">Wes Dorrance</div>
          <div class="person__title">CREATOR</div>
        </div>
        <div class="contact">123.456.7890 | dorrance@brindleharrow.com | www.brindleharrowsauce.com</div>
        <div class="social">
          <span class="social__item" aria-label="Quillo"><span class="social__mark"></span>@getbrindleharrow</span>
          <span class="social__item" aria-label="Lumigrid"><span class="social__mark"></span>getbrindleharrow</span>
          <span class="social__item" aria-label="Pagora"><span class="social__mark"></span>getbrindleharrow</span>
        </div>
      </div>
    </div>
  </div>
</body>
</html>
```